New App: 4 Page Design - Updated Brief

We need an indicative design for our new app 'Kit Runner', a delivery service for tools and hardware in Sydney, Australia.

Imagine a service which copies the blue print of Zolvo Meals, but for tools and Hardware. Where builders and tradespeople are stuck on-site at work and need a tool to be delivered to them on-site, same day. They can jump onto this app and in-put their address, then select an item from the catalogue and confirm the order. Once the order has been collected and due for delivery a map will show the location of the delivery driver.

We'd like 4 pages designed.

1st page) Loading page, similar to but not the same as the ZolvoMeals example attached.

2nd page) Home page - featuring the logo and some icons which direct users around the website. (Please see link to design example: https://www.zolvomeals.example/au?ref_id=a1b2c3d4-e5f6-47a8-9b0c-d1e2f3a4b5c6 )

3rd page) A page which depicts the catalogue of tools and hardware (showing generic tools available (Please see link to design example https://www.trellmart.example/products/building-hardware).

4th page) We'd like a page which shows a map, tracking the delivery, from the hardware store, to the location of the purchaser, exactly like any typical zolvo delivery service.

Please see the below website for design guidance and ideas

https://www.trellmart.example/?src=ab.cd&ref=Xy7QpLm3Rt9Vw2KsNh4Bf8JdZc6GaT1YeUo5Mi0Wq3ErPx7Ls2Dn9Hv4Ck8Fj6Bg1Az5Tm3Ry0Qu7Wp2Xo4Zi9Ke6Jl8Nb3Vc1Sd5Ph7Mf_abc

Target Market(s)

Construction industry, tradespeople

Industry/Entity Type

Construction and Tradesmen

Colors

Designer to choose colors to be used in the design.

Requirements
Must have
• Desired Colour schemes: up to the designer but no bright colours
Nice to have
• An icon bar at the bottom of the page that directs you to the various pages on the app. Example shown in the attachments
Should not have
• An exact copy of the Zolvo App

```html
<!DOCTYPE html>
<html lang="en">
<head>
<meta charset="utf-8">
<title>Kit Runner – Catalogue</title>
<link rel="stylesheet" href="https://fonts.googleapis.com/css2?family=Inter:wght@600;700;800&display=swap">
<style>
  :root {
    --teal: #0f5257;
    --ink: #0b1a1c;
    --paper: #ffffff;
  }
  * { margin: 0; padding: 0; box-sizing: border-box; }
  html, body { width: 1200px; height: 2597px; overflow: hidden; background: var(--paper); }
  body { position: relative; font-family: "Inter", sans-serif; color: var(--ink); }

  .page-header { position: absolute; left: 0; top: 215px; width: 1200px; height: 140px; }
  .page-header .accent { position: absolute; left: 0; top: 0; width: 49px; height: 139px; background: var(--teal); }
  .page-title { position: absolute; left: 112px; top: -12px; font-size: 90px; font-weight: 700; letter-spacing: -1px; color: var(--teal); line-height: 1.1; }
  .page-subtitle { position: absolute; left: 114px; top: 96px; font-size: 44px; font-weight: 700; letter-spacing: 0.32em; color: var(--teal); line-height: 1; }

  .category { position: absolute; left: 0; width: 1200px; height: 120px; display: flex; align-items: center; }
  .category .chevron { position: absolute; left: 48px; width: 52px; height: 52px; }
  .category .label { position: absolute; left: 121px; font-size: 71px; font-weight: 700; letter-spacing: -0.5px; white-space: nowrap; }

  .subcategory { position: absolute; left: 188px; font-size: 47px; font-weight: 700; letter-spacing: 0.04em; line-height: 1; transform: translateY(-50%); }

  .fade { position: absolute; left: 0; top: 2270px; width: 1200px; height: 90px; background: linear-gradient(rgba(255,255,255,0), rgba(255,255,255,0.85)); }

  .tab-bar { position: absolute; left: 0; top: 2351px; width: 1200px; height: 246px; background: var(--teal); }
  .tab-bar .tab { position: absolute; top: 89px; width: 72px; height: 72px; }
</style>
</head>
<body>
  <header class="page-header">
    <div class="accent"></div>
    <h1 class="page-title">Catalogue</h1>
    <p class="page-subtitle">BUILDING &amp; HARDWARE</p>
  </header>

  <div class="category" style="top:412px">
    <svg class="chevron" viewBox="0 0 52 52"><path d="M6 16 L26 36 L46 16" fill="none" stroke="var(--teal)" stroke-width="7" stroke-linecap="round" stroke-linejoin="round"/></svg>
    <span class="label">Timber</span>
  </div>

  <span class="subcategory" style="top:614px">TIMBER BOARDS</span>
  <span class="subcategory" style="top:731px">DECKING</span>
  <span class="subcategory" style="top:848px">RETAINING WALLS</span>
  <span class="subcategory" style="top:965px">FRAMING TIMBER</span>
  <span class="subcategory" style="top:1082px">TIMBER MOULDINGS</span>
  <span class="subcategory" style="top:1199px">DRESSED TIMBER</span>

  <div class="category" style="top:1272px">
    <svg class="chevron" viewBox="0 0 52 52"><path d="M16 6 L36 26 L16 46" fill="none" stroke="var(--teal)" stroke-width="7" stroke-linecap="round" stroke-linejoin="round"/></svg>
    <span class="label">Building Materials &amp; Supplies</span>
  </div>
  <div class="category" style="top:1441px">
    <svg class="chevron" viewBox="0 0 52 52"><path d="M16 6 L36 26 L16 46" fill="none" stroke="var(--teal)" stroke-width="7" stroke-linecap="round" stroke-linejoin="round"/></svg>
    <span class="label">Building Boards</span>
  </div>
  <div class="category" style="top:1610px">
    <svg class="chevron" viewBox="0 0 52 52"><path d="M16 6 L36 26 L16 46" fill="none" stroke="var(--teal)" stroke-width="7" stroke-linecap="round" stroke-linejoin="round"/></svg>
    <span class="label">Fasteners &amp; Fixings</span>
  </div>
  <div class="category" style="top:1779px">
    <svg class="chevron" viewBox="0 0 52 52"><path d="M16 6 L36 26 L16 46" fill="none" stroke="var(--teal)" stroke-width="7" stroke-linecap="round" stroke-linejoin="round"/></svg>
    <span class="label">Steel &amp; Aluminium Sections</span>
  </div>
  <div class="category" style="top:1948px">
    <svg class="chevron" viewBox="0 0 52 52"><path d="M16 6 L36 26 L16 46" fill="none" stroke="var(--teal)" stroke-width="7" stroke-linecap="round" stroke-linejoin="round"/></svg>
    <span class="label">Fencing &amp; Gates</span>
  </div>
  <div class="category" style="top:2117px">
    <svg class="chevron" viewBox="0 0 52 52"><path d="M16 6 L36 26 L16 46" fill="none" stroke="var(--teal)" stroke-width="7" stroke-linecap="round" stroke-linejoin="round"/></svg>
    <span class="label">Door Hardware</span>
  </div>
  <div class="category" style="top:2286px">
    <svg class="chevron" viewBox="0 0 52 52"><path d="M16 6 L36 26 L16 46" fill="none" stroke="var(--teal)" stroke-width="7" stroke-linecap="round" stroke-linejoin="round"/></svg>
    <span class="label">General Hardware</span>
  </div>
  <div class="fade"></div>

  <nav class="tab-bar">
    <svg class="tab" style="left:112px" viewBox="0 0 72 72"><path d="M6 18 H66 M6 36 H66 M6 54 H66" stroke="#fff" stroke-width="5" stroke-linecap="round"/></svg>
    <svg class="tab" style="left:333px" viewBox="0 0 72 72" fill="none" stroke="#fff" stroke-width="5" stroke-linejoin="round" stroke-linecap="round"><path d="M46 8 H10 V64 H58 V34"/><path d="M54 6 L64 16 L38 42 L26 46 L30 34 Z"/><path d="M18 24 H34 M18 38 H24"/></svg>
    <svg class="tab" style="left:564px" viewBox="0 0 72 72" fill="none" stroke="#fff" stroke-width="5" stroke-linejoin="round"><path d="M8 32 L36 8 L64 32 V64 H8 Z"/><path d="M28 64 V42 H44 V64"/></svg>
    <svg class="tab" style="left:795px" viewBox="0 0 72 72" fill="none" stroke="#fff" stroke-width="5" stroke-linejoin="round" stroke-linecap="round"><path d="M4 8 H14 L22 44 H60 L66 18 H17"/><path d="M22 44 L20 54 H62"/><circle cx="26" cy="64" r="4"/><circle cx="56" cy="64" r="4"/></svg>
    <svg class="tab" style="left:1019px" viewBox="0 0 72 72" fill="none" stroke="#fff" stroke-width="5" stroke-linejoin="round"><circle cx="36" cy="22" r="14"/><path d="M6 66 V60 C6 48 18 42 36 42 C54 42 66 48 66 60 V66 Z"/></svg>
  </nav>
</body>
</html>
```